Business Card Design needed - Something Awesome!

Need a business card designed. Company is "Marlowe Advisory" we do consulting and also have sales automation technology.
I'm going to use thick stock or metal, something really nice... I was thinking about a QR Code on the back that would just upload my contact info to the persons contact, etc -

This is a Strategy Company with a tech feel. I'm open to ideas but really want this to be nice!

I need a template that should include:

Name | Position or Title
D: 415.902.3376
www.marloweadvisory.example

I'm going to attach my contact so you can use that one, I need to get this printed.

Target Market(s)

Small to mid size customers, Entrepreneurs etc.

Industry/Entity Type

Consulting, Tech, Private Equity.

Contact Information for Business Card

Name, Phone, Maybe email, URL

Font styles to use
Sans Serif

Colors

Designer to choose only greyscale colors for use in the design.

Requirements
Must have
• Fresh, Clean, stand out from the crowd - will be on thick stock or metal.
Nice to have
• Clean, simple yet impactful.
Should not have
• Not cartoonish

```html
<!DOCTYPE html>
<html lang="en">
<head>
<meta charset="utf-8">
<title>Marlowe Advisory – Business Card</title>
<link rel="stylesheet" href="https://fonts.googleapis.com/css2?family=Montserrat:wght@400;500;600;700&display=swap">
<style>
  :root {
    --ink: #000000;
    --paper: #ffffff;
    --backdrop: #2a2a2a;
    --shadow: rgba(0, 0, 0, 0.55);
  }
  * { margin: 0; padding: 0; box-sizing: border-box; }
  html, body {
    width: 1093px;
    height: 1200px;
    overflow: hidden;
    background: var(--backdrop);
    font-family: "Montserrat", sans-serif;
  }
  .card {
    position: absolute;
    left: 264px;
    width: 578px;
    height: 357px;
    overflow: hidden;
    box-shadow: 3px 4px 8px var(--shadow);
  }
  .card--front { top: 226px; background: var(--paper); }
  .card--back { top: 620px; background: var(--ink); }

  .card__band {
    position: absolute;
    inset: 0;
    width: 578px;
    height: 357px;
  }
  .brand-name {
    position: absolute;
    font-weight: 600;
    letter-spacing: 0.02em;
    white-space: nowrap;
    line-height: 1;
  }
  .card--front .brand-name {
    left: 25px;
    top: 56px;
    font-size: 30px;
    color: var(--ink);
  }
  .card--back .brand-name {
    left: 0;
    right: 0;
    top: 156px;
    text-align: center;
    font-size: 44px;
    color: var(--paper);
  }
  .contact {
    position: absolute;
    left: 26px;
    top: 152px;
    color: var(--paper);
  }
  .contact__name {
    font-size: 20px;
    font-weight: 700;
    letter-spacing: 0.01em;
    line-height: 1;
  }
  .contact__title {
    font-size: 15px;
    font-weight: 400;
    margin-top: 3px;
  }
  .contact__rule {
    width: 40px;
    height: 1px;
    background: var(--paper);
    margin: 13px 0 14px;
  }
  .contact__line {
    display: flex;
    align-items: center;
    gap: 6px;
    font-size: 15px;
    line-height: 21px;
  }
  .contact__icon { width: 16px; height: 14px; flex: none; }
  .website {
    position: absolute;
    left: 27px;
    top: 300px;
    font-size: 15px;
    color: var(--ink);
  }
</style>
</head>
<body>
  <section class="card card--front">
    <svg class="card__band" viewBox="0 0 578 357" aria-hidden="true">
      <polygon points="0,117 425,117 296,287 0,287" fill="var(--ink)"/>
    </svg>
    <div class="brand-name">MARLOWE ADVISORY</div>
    <div class="contact">
      <div class="contact__name">DANIEL REYES</div>
      <div class="contact__title">Managing Director</div>
      <div class="contact__rule"></div>
      <div class="contact__line">
        <svg class="contact__icon" viewBox="0 0 16 16" aria-hidden="true">
          <path d="M3.5 1.5 L6 4.5 L4.6 6.2 C5.6 8.3 7.7 10.4 9.8 11.4 L11.5 10 L14.5 12.5 L13 14.5 C7 14 2 9 1.5 3 Z" fill="none" stroke="var(--paper)" stroke-width="1.6" stroke-linejoin="round"/>
        </svg>
        <span>415.902.3376</span>
      </div>
      <div class="contact__line">
        <svg class="contact__icon" viewBox="0 0 16 12" aria-hidden="true">
          <rect x="0.5" y="0.5" width="15" height="11" fill="var(--paper)"/>
          <path d="M0.5 0.5 L8 7 L15.5 0.5 M0.5 11.5 L6 6 M15.5 11.5 L10 6" fill="none" stroke="var(--ink)" stroke-width="1"/>
        </svg>
        <span>info@marloweadvisory.example</span>
      </div>
    </div>
    <div class="website">www.marloweadvisory.example</div>
  </section>

  <section class="card card--back">
    <div class="brand-name">MARLOWE ADVISORY</div>
  </section>
</body>
</html>
```